Wordpress Design Project

Hi,

I would like a more modern colourful design doing for my website ZAP Lnx (www.za%plnx.com - remove percentage). But I do still want to keep the same sort of colors, just maybe lighter. More interesting.

I want the inside pages to NOT all look the same with just boring text.

I want the site to look more appealing and maybe a new logo.
Updates

I would like to mention I would prefer to keep the same logo after rethinking it (possibly a slight refresh of the logo if you feel its a good idea) and the same color scheme as at present.

Saves us rebranding a lot of our apps, tools online ads etc.

Also I thought it is worth mentioning we have 2 parts to the site. The front end and the logged in area. It would be good if when making the front end you keep in mind the back end at http://p.za%plnx.com (remove percentage). We can only edit this limitedly (can edit the entire footer, the logo and full CSS of it). Would be good if we could make sure the header and footer can be used on the back end as well maybe to make it match.

I also want layouts making not just for the homepage. Obviously every page will basically be the same but I don't want all the other pages to just be 'text' and no real layout.

You can see out main pages on the website at the moment, I want those other pages to be laid out nice and differently as well. For example the testimonials page could be more interesting with speech bubbles and pictures of each person (just use placeholders). The affiliates page could be a description and then a nice fancy list of features why to join etc. 

Nothing overly complicated but I think it makes the whole site seem a lot better.

Target Market(s)

Affiliate Marketing. International.

Requirements
Must have
• Needs to be more room for links across the navigation at the top, also sub menus (at present we have a lot of pages which are hidden deep within other pages).
Nice to have
• Lists of features for advertisers and affiliates on the homepage part.

Menu items and buttons have nice hover over effects.

I want to get across on our pages all the different unique features we have.

Maybe some kind of slider which has past offer logos in, just use example logos.

```html
<!DOCTYPE html>
<html lang="en">
<head>
<meta charset="utf-8">
<title>ZAP Lnx – International Affiliate Network</title>
<link href="https://fonts.googleapis.com/css2?family=Arimo:ital,wght@0,400;0,700;1,400&display=swap" rel="stylesheet">
<style>
:root{
  --page-bg:#f1f1f1;
  --page-bg-low:#f7f7f7;
  --column:#ffffff;
  --header-blue:#3d8fc4;
  --header-blue-light:#8cc4e4;
  --orange:#f7941d;
  --orange-dark:#e2700f;
  --orange-text:#e87511;
  --heading-blue:#1f6fa6;
  --text:#555555;
  --text-soft:#777777;
  --panel-grey:#e4e4e4;
  --panel-border:#d6d6d6;
  --button-grey:#8b8d90;
  --button-dark:#3a3a3a;
  --footer:#3b3b3b;
  --footer-text:#e0e0e0;
  --dot-dark:#3f3f3f;
}
*{box-sizing:border-box;margin:0;padding:0}
html,body{width:1200px;height:1127px;overflow:hidden}
body{font-family:"Arimo",Arial,sans-serif;color:var(--text);background:linear-gradient(var(--page-bg) 0 520px,var(--page-bg-low) 520px);position:relative}
.abs{position:absolute}
.column{left:90px;top:0;width:1020px;height:1127px;background:var(--column);border-left:1px solid #e3e3e3;border-right:1px solid #e3e3e3}
.header{left:95px;top:5px;width:1010px;height:172px;background:linear-gradient(100deg,#2f7fb8 0%,var(--header-blue) 35%,var(--header-blue-light) 55%,var(--header-blue) 80%,#2f80ba 100%)}
.brand-name{left:112px;top:24px;font-size:44px;font-weight:700;color:#ffffff;line-height:1}
.tagline{left:114px;top:80px;font-size:12px;font-weight:700;letter-spacing:3px;color:#ffffff}
.call{right:109px;top:23px;font-size:17px;font-weight:700;color:#ffffff}
.top-btn{top:61px;height:29px;background:linear-gradient(var(--orange),var(--orange-dark));color:#fff;font-size:14px;line-height:27px;text-align:center;border:1px solid #d86a10}
.search{left:872px;top:61px;width:220px;height:29px;background:#fff;border:1px solid #c9c9c9;font-size:11px;color:#666;padding:8px 12px}
.search svg{position:absolute;right:10px;top:6px}
.nav{left:103px;top:118px;width:994px;height:52px;background:linear-gradient(var(--orange),var(--orange-dark));display:flex;border-radius:3px 3px 0 0}
.nav a{color:#fff;font-size:14.5px;font-weight:700;text-decoration:none;display:flex;align-items:center;justify-content:center;border-right:1px solid #f9b25e}
.nav a.current{background:linear-gradient(#f28a1f,#e06410)}
.hero{left:103px;top:177px;width:994px;height:339px;background:#fff;border-radius:0 0 4px 4px;box-shadow:0 2px 6px rgba(0,0,0,.08)}
.hero-title{left:137px;top:226px;font-size:25px;font-weight:700;color:var(--heading-blue)}
.hero-copy{left:137px;top:266px;width:455px;font-size:13.5px;line-height:23px;color:var(--text)}
.hero-copy p{margin-bottom:12px}
.hero-copy .lead{color:var(--orange-text)}
.btn-grey{background:linear-gradient(#a2a4a7,var(--button-grey));color:#fff;font-weight:700;font-size:15px;text-align:center;border:1px solid #7d7f82;border-radius:3px}
.view-more{left:138px;top:411px;width:113px;height:38px;line-height:36px}
.dots{left:138px;top:475px;display:flex;gap:7px}
.dots span{width:15px;height:15px;border-radius:50%;background:var(--dot-dark)}
.dots span:first-child{background:var(--orange-dark)}
.map{left:610px;top:186px;width:480px;height:320px;background:radial-gradient(ellipse at 55% 45%,#d9d9d9 0%,#e9e9e9 55%,#ffffff 80%)}
.intro{left:120px;top:545px;width:965px;font-size:14.5px;line-height:23px;font-style:italic;color:var(--text-soft)}
.rule{left:120px;top:631px;width:965px;height:1px;background:#e4e4e4}
.card{background:#fff;border:1px solid #e2e2e2;box-shadow:inset 0 0 0 5px #f6f6f6}
.card h2{position:absolute;left:20px;top:17px;font-size:18px;font-weight:700;color:var(--heading-blue)}
.card ul{position:absolute;left:22px;top:58px;list-style:none}
.card li{font-size:13.5px;height:36.5px;display:flex;gap:10px;color:var(--text)}
.card li svg{margin-top:4px}
.sign-up{width:123px;height:30px;line-height:28px}
.panel{background:linear-gradient(var(--panel-grey),#f4f4f4);border:1px solid var(--panel-border);border-radius:3px}
.panel h2{position:absolute;left:48px;top:21px;font-size:18px;font-weight:700;color:var(--heading-blue)}
.panel .icon{position:absolute;left:12px;top:10px}
.field-label{font-size:12.5px;color:#555;text-align:right;width:80px}
.field{background:#fff;border:1px solid #c8c8c8;width:217px;height:30px}
.login-btn{width:77px;height:30px;line-height:28px;font-size:14px;background:linear-gradient(#555,var(--button-dark));color:#fff;text-align:center;border-radius:3px;border:1px solid #222}
.news-body{left:7px;top:54px;width:297px;height:98px;background:#fff;border:1px solid #d8d8d8;padding:14px 12px 0 28px}
.news-body h3{font-size:13.5px;font-weight:400;color:var(--orange-text);margin-bottom:5px;position:relative}
.news-body h3::before{content:"»";position:absolute;left:-18px;top:-2px;font-size:16px}
.news-body p{font-size:12.5px;line-height:19px;color:#666}
.footer{left:95px;top:1032px;width:1010px;height:95px;background:var(--footer);color:var(--footer-text);font-size:12.5px}
.footer-links{left:16px;top:22px;display:flex}
.footer-links a{color:var(--footer-text);text-decoration:none}
.footer-links span{margin:0 10px}
.copyright{left:16px;top:59px;word-spacing:1px}
.social{top:36px;width:24px;height:24px;border-radius:3px}
</style>
</head>
<body>
<div class="abs column"></div>

<header class="abs header"></header>
<div class="abs brand-name">ZAP Lnx</div>
<div class="abs tagline">EARN MONEY &amp; INCREASE SALES</div>
<div class="abs call">Call us : +44 (0)1632 960471</div>
<div class="abs top-btn" style="left:719px;width:69px">LOG IN</div>
<div class="abs top-btn" style="left:793px;width:74px">SIGN UP</div>
<div class="abs search">Search
  <svg width="16" height="16" viewBox="0 0 16 16"><circle cx="6" cy="6" r="4.5" fill="none" stroke="#222" stroke-width="2"/><line x1="9.5" y1="9.5" x2="14.5" y2="14.5" stroke="#222" stroke-width="3" stroke-linecap="round"/></svg>
</div>

<nav class="abs nav">
  <a class="current" style="width:111px">HOME</a>
  <a style="width:131px">ABOUT US</a>
  <a style="width:133px">OUR BLOG</a>
  <a style="width:163px">TESTIMONIALS</a>
  <a style="width:136px">AFFILIATES</a>
  <a style="width:161px">ADVERTISERS</a>
  <a style="width:159px;border-right:0">CONTACT US</a>
</nav>

<section class="abs hero"></section>
<div class="abs map" role="img" aria-label="Dotted world map with an affiliate manager figure and arrows reaching out to markets on each continent"></div>
<h1 class="abs hero-title">International Affiliate Network</h1>
<div class="abs hero-copy">
  <p><span class="lead">Welcome to the ZAP Lnx affiliate network.</span> On time payments, hot &amp; exclusive CPL/CPA offers, fast support and low fees for advertisers, is the making of a leading affiliate network!</p>
  <p>ZAP Lnx offer a wide range of advertisers for your websites. So you can start monetizing your traffic or get an additional revenue stream, today.</p>
</div>
<div class="abs btn-grey view-more">View more</div>
<div class="abs dots"><span></span><span></span><span></span><span></span></div>

<p class="abs intro">ZAP Lnx Affiliate Network we focus on lead generation offers. We have a range of competitions, surveys, incentives and gambling offers. Whatever the industry, you will be able to find offers to suit your traffic.ZAP Lnx is a powerful performance-based internet marketing network dedicated to advertisers to affiliates through its powerful affiliate network..</p>
<div class="abs rule"></div>

<section class="abs card" style="left:105px;top:656px;width:662px;height:173px">
  <h2>Affiliates</h2>
  <ul>
    <li><svg width="14" height="10" viewBox="0 0 14 10"><path d="M1 3h7V0l6 5-6 5V7H1z" fill="#b5b5b5"/></svg>Get access to a wide range of top performing offers for your websites and email marketing lists.</li>
    <li><svg width="14" height="10" viewBox="0 0 14 10"><path d="M1 3h7V0l6 5-6 5V7H1z" fill="#b5b5b5"/></svg>Fresh and exclusive offers to promote.</li>
    <li><svg width="14" height="10" viewBox="0 0 14 10"><path d="M1 3h7V0l6 5-6 5V7H1z" fill="#b5b5b5"/></svg>Join over 2,000 affiliates already signed up to ZAP Lnx.</li>
  </ul>
  <div class="abs btn-grey sign-up" style="left:523px;top:125px">Sign up Now</div>
</section>

<section class="abs card" style="left:105px;top:845px;width:662px;height:172px">
  <h2>Advertisers</h2>
  <ul>
    <li><svg width="14" height="10" viewBox="0 0 14 10"><path d="M1 3h7V0l6 5-6 5V7H1z" fill="#b5b5b5"/></svg>Generate sales/leads to your website instantly with the ZAP Lnx Affiliate Network.</li>
    <li><svg width="14" height="10" viewBox="0 0 14 10"><path d="M1 3h7V0l6 5-6 5V7H1z" fill="#b5b5b5"/></svg>Only pay on performance, no monthly or setup fees.</li>
    <li><svg width="14" height="10" viewBox="0 0 14 10"><path d="M1 3h7V0l6 5-6 5V7H1z" fill="#b5b5b5"/></svg>ZAP Lnx takes the risk out of advertising.</li>
  </ul>
  <div class="abs btn-grey sign-up" style="left:523px;top:124px">Sign up Now</div>
</section>

<section class="abs panel" style="left:783px;top:657px;width:312px;height:191px">
  <svg class="icon" width="28" height="34" viewBox="0 0 28 34"><path d="M7 15V10a7 7 0 0 1 14 0v5" fill="none" stroke="#8a9aa8" stroke-width="3"/><rect x="3" y="15" width="22" height="17" rx="2" fill="#9fb0bf"/></svg>
  <h2>Account Login</h2>
  <div class="abs" style="left:0;top:59px;width:310px;height:1px;background:#d2d2d2"></div>
  <div class="abs field-label" style="left:0;top:73px">Email :</div>
  <div class="abs field" style="left:83px;top:64px"></div>
  <div class="abs field-label" style="left:0;top:104px">Password :</div>
  <div class="abs field" style="left:83px;top:101px"></div>
  <div class="abs login-btn" style="left:221px;top:146px">LOG IN</div>
</section>

<section class="abs panel" style="left:783px;top:857px;width:312px;height:159px">
  <svg class="icon" style="top:14px" width="28" height="24" viewBox="0 0 28 24"><rect x="2" y="12" width="4" height="10" fill="#9fb0bf"/><rect x="8" y="6" width="4" height="16" fill="#9fb0bf"/><rect x="14" y="9" width="4" height="13" fill="#9fb0bf"/><rect x="20" y="3" width="4" height="19" fill="#9fb0bf"/><rect x="0" y="22" width="28" height="2" fill="#8a9aa8"/></svg>
  <h2 style="left:50px">Latest News</h2>
  <svg class="abs" style="left:277px;top:24px" width="17" height="17" viewBox="0 0 17 17"><circle cx="8.5" cy="8.5" r="8.5" fill="#9a9a9a"/><path d="M7 5l4 3.5L7 12" fill="none" stroke="#fff" stroke-width="2"/></svg>
  <div class="abs news-body">
    <h3>Curabitur congue odio vitae</h3>
    <p>Ligula semper ac auctor justo tincidunt. unc placerat sodales massa non molestie.</p>
  </div>
</section>

<footer class="abs footer">
  <div class="abs footer-links">
    <a>Home</a><span>|</span><a>About Us</a><span>|</span><a>Our Blog</a><span>|</span><a>Testimonials</a><span>|</span><a>Affiliates</a><span>|</span><a>Advertisers</a><span>|</span><a>Contact Us</a>
  </div>
  <div class="abs copyright">Copyright &nbsp;©&nbsp; 2013 &nbsp;&nbsp; www.zaplnx.com &nbsp;&nbsp; All rights reserved.</div>
  <div class="abs social" style="left:936px;background:#3b5d9c"></div>
  <div class="abs social" style="left:967px;background:#3fa9dd"></div>
</footer>
</body>
</html>
```